Business Card Design for BrightvaleMedia.com

--I need a business card design for my company BrightvaleMedia.com

I have attached my logo...I want the brightvale media logo on the front of the business card, and then I want The Quillstone Chief on the back of it with my information.

I would like to see a light colored background as well as a dark colored background

FRONT:
BRIGHTVALE MEDIA LOGO
248 N. Larkmoor
3rd Floor
San Diego CA 92173
www.BrightvaleMedia.com

Advanced Website & App Development
Websites, Apps, Online Voucher Systems

Leading Edge Marketing Services
SMS, VB, SMM, SEM,

BACK:
QUILLSTONE CHIEF LOGO
Dorian Pelletta
The Quillstone Chief
Call Or Text: 619-555-0148
Dorian@QuillstoneChief.example
www.QuillstoneChief.example

Target Market(s)

small business owners

Industry/Entity Type

Business Consultant

Contact Information for Business Card

FRONT:
BRIGHTVALE MEDIA LOGO
248 N. Larkmoor
3rd Floor
San Diego CA 92173
www.BrightvaleMedia.com

SMS, VB, SMM, SEM,

BACK:
QUILLSTONE CHIEF LOGO
Dorian Pelletta
The Quillstone Chief
Dorian@QuillstoneChief.example
www.QuillstoneChief.example

Requirements
Must have
• add this quote on it somewhere, anywhere,preferrably on back
• "The Fastest Way To Success Is To Take Action”
• — Dorian Pelletta, Quillstone Chief
Nice to have
• open
Should not have
• red

```html
<!DOCTYPE html>
<html lang="en">
<head>
<meta charset="utf-8">
<title>Brightvale Media — Business Cards</title>
<link rel="stylesheet" href="https://fonts.googleapis.com/css2?family=Lato:ital,wght@0,400;0,700;0,900;1,400&display=swap">
<style>
  :root {
    --backdrop: #141414;
    --card-white: #ffffff;
    --band-grey: #6d6e71;
    --band-blue: #0a6fa8;
    --brand-blue: #0b6aa6;
    --quote-grey: #6d6e71;
    --text-light: #ffffff;
  }
  html, body {
    margin: 0;
    width: 1200px;
    height: 900px;
    overflow: hidden;
    background: var(--backdrop);
  }
  .canvas {
    position: relative;
    width: 1200px;
    height: 900px;
    font-family: "Lato", Arial, sans-serif;
  }
  .card {
    position: absolute;
    top: 306px;
    height: 271px;
    border-radius: 12px;
    overflow: hidden;
    background: var(--card-white);
    display: flex;
    flex-direction: column;
  }
  .card--chief { left: 149px; width: 439px; }
  .card--media { left: 608px; width: 441px; }

  .card__head {
    display: flex;
    flex-direction: column;
    align-items: center;
    justify-content: center;
    text-align: center;
  }
  .card--chief .card__head { height: 118px; }
  .card--media .card__head { height: 114px; }

  .wordmark {
    margin: 0;
    color: var(--brand-blue);
    font-family: "Lato", Arial, sans-serif;
    font-weight: 700;
    font-size: 25px;
    letter-spacing: 3px;
    line-height: 30px;
  }

  .quote {
    margin: 8px 0 0;
    color: var(--quote-grey);
    font-size: 11px;
    line-height: 14px;
  }
  .quote__text { font-style: italic; display: block; }
  .quote__source { display: block; font-size: 10px; }

  .card__band {
    background: var(--band-grey);
    color: var(--text-light);
    text-align: center;
    display: flex;
    flex-direction: column;
    justify-content: center;
  }
  .card--chief .card__band { height: 60px; }
  .card--media .card__band { height: 95px; }

  .card__rule { height: 4px; background: var(--card-white); }

  .card__foot {
    flex: 1;
    background: var(--band-blue);
    color: var(--text-light);
    text-align: center;
    display: flex;
    flex-direction: column;
    justify-content: center;
    font-size: 12px;
    line-height: 16px;
  }

  .person__name {
    margin: 0;
    font-weight: 900;
    font-size: 16px;
    letter-spacing: 1.5px;
    line-height: 20px;
    text-transform: uppercase;
  }
  .person__title { margin: 0; font-size: 12px; line-height: 16px; }

  .contact { margin: 0; }
  .contact b { font-weight: 900; }

  .service { margin: 0; font-size: 12px; line-height: 16px; }
  .service + .service { margin-top: 6px; }

  .address {
    margin: 0;
    display: flex;
    align-items: center;
    justify-content: center;
    gap: 3px;
  }
  .address svg { width: 9px; height: 13px; fill: var(--text-light); }
</style>
</head>
<body>
<main class="canvas">

  <section class="card card--chief" aria-label="Quillstone Chief card">
    <header class="card__head">
      <h1 class="wordmark">QUILLSTONE CHIEF</h1>
      <p class="quote">
        <span class="quote__text">“The Fastest Way To Success Is To Take Action”</span>
        <span class="quote__source">— Dorian Pelletta, Quillstone Chief</span>
      </p>
    </header>
    <div class="card__band">
      <p class="person__name">Dorian Pelletta</p>
      <p class="person__title">The Quillstone Chief</p>
    </div>
    <div class="card__rule"></div>
    <div class="card__foot">
      <p class="contact"><b>P:</b> 619-555-0148</p>
      <p class="contact"><b>E:</b> Dorian@QuillstoneChief.example</p>
      <p class="contact"><b>W:</b> www.QuillstoneChief.example</p>
    </div>
  </section>

  <section class="card card--media" aria-label="Brightvale Media card">
    <header class="card__head">
      <h1 class="wordmark">BRIGHTVALE MEDIA</h1>
    </header>
    <div class="card__band">
      <p class="service">Advanced Website &amp; App Development<br>Websites, Apps, Online Voucher Systems</p>
      <p class="service">Leading Edge Marketing Services<br>SMS, VB, SMM, SEM,</p>
    </div>
    <div class="card__rule"></div>
    <div class="card__foot">
      <p class="address">
        <svg viewBox="0 0 10 14" aria-hidden="true"><path d="M5 0C2.2 0 0 2.2 0 5c0 3.6 5 9 5 9s5-5.4 5-9C10 2.2 7.8 0 5 0zm0 7a2 2 0 1 1 0-4 2 2 0 0 1 0 4z"/></svg>
        248 N. Larkmoor&nbsp; 3rd Floor, San Diego CA 92173
      </p>
      <p class="contact">www.BrightvaleMedia.com</p>
    </div>
  </section>

</main>
</body>
</html>
```